Tovel & Associates - London New Letting and Property Management Company *

Tovel & Associates LTD is a new company based in London, and works with brand new residential property in the city centre.

We are aiming to have 1000 new properties a year.

We are looking for something modern and minimalistic :
Logo ,Monogram, Paper Head and Business Card.

Target Market(s)

Internation landlords

Industry/Entity Type

Real Estate

Logo Text

Tovel & Associates

Colors

Designer to choose colors to be used in the design.

Requirements
Nice to have
• A particular monogram with "TA"
Should not have
• Little House over the logo

```html
<!DOCTYPE html>
<html lang="en">
<head>
<meta charset="utf-8">
<title>Tovel &amp; Associates — Business Card</title>
<link href="https://fonts.googleapis.com/css2?family=Montserrat:wght@400;500;600;700&display=swap" rel="stylesheet">
<style>
  :root {
    --backdrop: #2b2623;
    --card-blue: #1d4f85;
    --card-blue-deep: #174476;
    --emboss-blue: #163d6a;
    --accent-blue: #2a9be0;
    --text-white: #ffffff;
    --text-soft: #dbe8f5;
  }
  * { margin: 0; padding: 0; box-sizing: border-box; }
  html, body {
    width: 1200px; height: 715px; overflow: hidden;
    background: var(--backdrop);
    font-family: "Montserrat", sans-serif;
  }
  .canvas {
    position: relative; width: 1200px; height: 715px;
  }
  .card {
    position: absolute; top: 209px;
    width: 520px; height: 297px;
    background: linear-gradient(160deg, var(--card-blue) 0%, var(--card-blue-deep) 100%);
    border-radius: 3px;
  }
  .card-front { left: 50px; }
  .card-back { left: 630px; }

  /* front: embossed company name */
  .front-brand {
    position: absolute; inset: 0;
    display: flex; flex-direction: column; align-items: center; justify-content: center;
    color: var(--emboss-blue);
  }
  .front-brand .brand-name { font-size: 30px; font-weight: 500; letter-spacing: 0.5px; }
  .front-brand .brand-suffix { font-size: 15px; font-weight: 500; letter-spacing: 3px; margin-top: 4px; }

  /* back */
  .back-brand {
    position: absolute; left: 0; top: 0; width: 290px; height: 100%;
    display: flex; flex-direction: column; align-items: center; justify-content: center;
    color: var(--text-white);
  }
  .back-brand .brand-mark {
    width: 34px; height: 34px; background: var(--text-white); margin-bottom: 14px;
  }
  .back-brand .brand-name { font-size: 23px; font-weight: 500; }
  .back-brand .brand-suffix { font-size: 13px; font-weight: 500; letter-spacing: 3px; margin-top: 4px; }

  .divider {
    position: absolute; left: 300px; top: 52px; width: 2px; height: 190px;
    background: var(--accent-blue);
  }
  .contact {
    position: absolute; left: 320px; top: 58px; color: var(--text-white);
  }
  .contact .person-name {
    font-size: 17px; font-weight: 700; color: var(--accent-blue); letter-spacing: 0.5px;
  }
  .contact .person-role {
    font-size: 12px; color: var(--accent-blue); margin-bottom: 12px;
  }
  .contact-list { list-style: none; }
  .contact-list li {
    display: flex; align-items: center; gap: 8px;
    font-size: 12.5px; line-height: 19px;
  }
  .contact-list svg { width: 10px; height: 10px; flex: none; }
  .contact-list .web-domain { color: var(--accent-blue); }
  .address { font-size: 12.5px; line-height: 18px; margin-top: 6px; }
</style>
</head>
<body>
<div class="canvas">

  <section class="card card-front">
    <div class="front-brand">
      <span class="brand-name">Tovel &amp; Associates</span>
      <span class="brand-suffix">LTD</span>
    </div>
  </section>

  <section class="card card-back">
    <div class="back-brand">
      <span class="brand-mark"></span>
      <span class="brand-name">Tovel &amp; Associates</span>
      <span class="brand-suffix">LTD</span>
    </div>

    <div class="divider"></div>

    <div class="contact">
      <p class="person-name">ELENA HARTLEY</p>
      <p class="person-role">Founder</p>
      <ul class="contact-list">
        <li>
          <svg viewBox="0 0 10 10"><rect x="2.5" y="0.5" width="5" height="9" rx="1" fill="none" stroke="#fff" stroke-width="1"/></svg>
          020 7946 0381
        </li>
        <li>
          <svg viewBox="0 0 10 10"><path d="M2 1 L4 1 L4.6 3 L3.4 4 Q4.5 6 6 6.6 L7 5.4 L9 6 L9 8 Q5 9 2 5 Q1 3 2 1Z" fill="#fff"/></svg>
          020 7946 0500
        </li>
        <li>
          <svg viewBox="0 0 10 10"><rect x="0.5" y="2" width="9" height="6" fill="none" stroke="#fff" stroke-width="1"/><path d="M0.5 2 L5 5.5 L9.5 2" fill="none" stroke="#fff" stroke-width="1"/></svg>
          info@tovelassociates.com
        </li>
        <li>
          <svg viewBox="0 0 10 10"><circle cx="5" cy="5" r="4.3" fill="none" stroke="#fff" stroke-width="1"/><ellipse cx="5" cy="5" rx="1.8" ry="4.3" fill="none" stroke="#fff" stroke-width="0.8"/><line x1="0.7" y1="5" x2="9.3" y2="5" stroke="#fff" stroke-width="0.8"/></svg>
          <span>www.<span class="web-domain">tovelassociates</span>.com</span>
        </li>
      </ul>
      <p class="address">48 Calder Row<br>London, EC2A 4NP</p>
    </div>
  </section>

</div>
</body>
</html>
```